Motel Sign - Front

(21/03/12 - I've edited the brief and removing the words "garden view" its not fitting in the designs I'm getting and just want the word motel to be the focus. I have a template/vision of what I want - see the whiteboard sketch of what I'm looking for uploaded today. Definitely open to creatively, new designs and different ideas but the whiteboard design I've done should be a guideline. Keep it fresh/green/white. use the sample photos of green as inspiration. Thanks)
We are a motel set in the mountain country of Victoria - Australia. The front of the motel needs a fresh look. We recently removed a large amount of the garden to expose a brick courtyard fence which the front of the courtyard faces out to the main road. Within the courtyard fence there is a wooden frame and paneling.
We want to have a new sign created to slot into the wooden frame. (see photo) its the white component.
Its a very large and unusual shape and I want to keep it simple but need to fill the in the best way possible.
The space is 940mm high and 4940mm width.
The message of the sign is simple the word "MOTEL". I want people to be able to drive past and glance in and see we are a motel straight away. So the main purpose of the sign is to say "MOTEL".
I am open to colour use to match the space and have impact. I thought a background colour should be 'off white'. I'm open to the colours used to match your design as long as it matches the brief. Maybe a garden green for the emblem.
IN BRIEF:
1) the word "MOTEL"
2) Border/Background that ties in the garden.
The design should be centred, clean and simple, doesn't have to fill the whole space as long as its balanced and centred.
I like cursive and garden like designs for this one - as long its the word MOTEL still has impact. (OPEN TO NEW IDEAS)
I am also open to different ideas and suggestions if you feel you have a better way to take advantage of this space.
The sign will be 7-8 metres from the road itself.
NOTE: the photos show the space and the painted white in the space where the sign will go. The garden in front of this space will be completely cleared.
Motel

```html
<!DOCTYPE html>
<html lang="en">
<head>
<meta charset="utf-8">
<title>Motel Sign</title>
<link rel="stylesheet" href="https://fonts.googleapis.com/css2?family=Jura:wght@300;400&display=swap">
<style>
  :root {
    --bg: #ffffff;
    --leaf-green: #8db43c;
    --leaf-soft: #cfe3a6;
    --leaf-pale: #eef5df;
    --lettering: #ffffff;
  }
  html, body {
    margin: 0;
    padding: 0;
    overflow: hidden;
    background: var(--bg);
  }
  .sign {
    position: relative;
    width: 1200px;
    height: 228px;
    background: var(--bg);
    overflow: hidden;
  }
  .flourish {
    position: absolute;
    top: 0;
    width: 370px;
    height: 228px;
  }
  .flourish--left {
    left: 0;
    background: radial-gradient(ellipse at 30% 45%, var(--leaf-soft) 0%, var(--leaf-pale) 55%, rgba(255,255,255,0) 80%);
  }
  .flourish--right {
    right: 0;
    background: radial-gradient(ellipse at 70% 55%, var(--leaf-soft) 0%, var(--leaf-pale) 55%, rgba(255,255,255,0) 80%);
  }
  .name-band {
    position: absolute;
    left: 190px;
    top: 73px;
    width: 830px;
    height: 72px;
    background: var(--leaf-green);
    display: flex;
    align-items: center;
    justify-content: center;
  }
  .name-band__word {
    margin: 0 0 0 -70px;
    font-family: "Jura", sans-serif;
    font-weight: 300;
    font-size: 90px;
    line-height: 1;
    letter-spacing: 6px;
    color: var(--lettering);
    transform: scaleX(1.18);
  }
</style>
</head>
<body>
  <main class="sign">
    <div class="flourish flourish--left" role="img" aria-label="Green swirling garden vine ornament with leaves"></div>
    <div class="flourish flourish--right" role="img" aria-label="Green swirling garden vine ornament with leaves"></div>
    <div class="name-band">
      <h1 class="name-band__word">MOTEL</h1>
    </div>
  </main>
</body>
</html>
```